Business Card Design

New business card design

Target Market(s)

Residential & Commercial Property Managers

Industry/Entity Type

Plumbing Services

Contact Information for Business Card

Name - Rowan Keddle, title - Director, Phone Number - 0431 286 517, email - rowan@tbk-plumbing.com.au, Company ABN - 73 215 904 386,

Font styles to use
Sans Serif

Colors
0054AA
0677BA
7BADD7
CADEEF
E8F1F8

```html
<!DOCTYPE html>
<html lang="en">
<head>
<meta charset="utf-8">
<title>TBK Plumbing – Business Card</title>
<link rel="stylesheet" href="https://fonts.googleapis.com/css2?family=Montserrat:wght@700&family=Roboto:wght@300;400&display=swap">
<style>
  :root {
    --backdrop: #2a2a2c;
    --card: #1d1e20;
    --accent: #1ba3e2;
    --ink: #ffffff;
    --ink-soft: #d6d8db;
    --ink-muted: #8a8d92;
  }
  * { margin: 0; padding: 0; box-sizing: border-box; }
  html, body { width: 1200px; height: 852px; overflow: hidden; }
  body {
    background: var(--backdrop);
    font-family: "Roboto", Arial, sans-serif;
    position: relative;
  }
  .card {
    position: absolute;
    width: 500px;
    height: 286px;
    border-radius: 18px;
    background: var(--card);
    overflow: hidden;
    box-shadow: 0 18px 40px rgba(0,0,0,.45);
  }
  .card--back { left: 80px; top: 283px; }
  .card--front { left: 620px; top: 283px; }

  .drop-pattern {
    position: absolute;
    inset: 0;
    background: linear-gradient(135deg, #0d0e10 0%, #2b2c2f 55%, #4a4b4f 100%);
  }

  .holder {
    position: absolute;
    left: 290px;
    top: 34px;
  }
  .holder__name {
    font-family: "Montserrat", Arial, sans-serif;
    font-weight: 700;
    font-size: 18px;
    color: var(--ink);
    letter-spacing: .2px;
  }
  .holder__title {
    font-size: 10px;
    color: var(--ink-muted);
    margin-top: 2px;
  }

  .contacts {
    position: absolute;
    left: 290px;
    top: 86px;
    list-style: none;
  }
  .contacts__item {
    display: flex;
    align-items: center;
    gap: 8px;
    font-size: 11px;
    font-weight: 300;
    color: var(--ink-soft);
    line-height: 17px;
  }
  .contacts__item svg { width: 10px; height: 10px; flex: none; }

  .contacts__address,
  .contacts__abn {
    position: absolute;
    left: 308px;
    font-size: 11px;
    font-weight: 300;
    color: var(--ink-soft);
    line-height: 16px;
  }
  .contacts__address { top: 146px; }
  .contacts__abn { top: 186px; }

  .brand {
    position: absolute;
    left: 34px;
    top: 160px;
    display: flex;
    align-items: center;
    gap: 10px;
  }
  .brand__dot {
    width: 11px;
    height: 11px;
    border-radius: 50%;
    background: var(--accent);
  }
  .brand__name {
    font-family: "Roboto", Arial, sans-serif;
    font-weight: 300;
    font-size: 30px;
    color: var(--ink);
    letter-spacing: 1px;
  }

  .company-band {
    position: absolute;
    right: 0;
    bottom: 0;
    width: 255px;
    height: 50px;
    background: var(--accent);
    border-top-left-radius: 22px;
    display: flex;
    align-items: center;
    justify-content: center;
    font-size: 11px;
    color: var(--ink);
  }
</style>
</head>
<body>

  <section class="card card--back">
    <div class="drop-pattern" role="img" aria-label="Repeating pattern of glossy black water droplets with one blue droplet"></div>
  </section>

  <section class="card card--front">
    <div class="holder">
      <h1 class="holder__name">Rowan Keddle</h1>
      <p class="holder__title">Director</p>
    </div>

    <ul class="contacts">
      <li class="contacts__item">
        <svg viewBox="0 0 10 10" aria-hidden="true"><path d="M2 1 L4 1 L4.6 3 L3.4 3.8 Q4.2 5.8 6.2 6.6 L7 5.4 L9 6 L9 8 Q5 9.5 1.5 5 Q0.5 3 2 1Z" fill="var(--ink-soft)"/></svg>
        0431 286 517
      </li>
      <li class="contacts__item">
        <svg viewBox="0 0 10 10" aria-hidden="true"><rect x="0.5" y="2" width="9" height="6" rx="0.8" fill="var(--ink-soft)"/><path d="M0.8 2.4 L5 5.6 L9.2 2.4" stroke="var(--card)" stroke-width="0.9" fill="none"/></svg>
        rowan@tbk-plumbing.com.au
      </li>
      <li class="contacts__item">
        <svg viewBox="0 0 10 10" aria-hidden="true"><circle cx="5" cy="5" r="4.2" fill="none" stroke="var(--ink-soft)" stroke-width="1"/><ellipse cx="5" cy="5" rx="1.8" ry="4.2" fill="none" stroke="var(--ink-soft)" stroke-width="0.8"/><line x1="0.8" y1="5" x2="9.2" y2="5" stroke="var(--ink-soft)" stroke-width="0.8"/></svg>
        www.tbk-plumbing.com.au
      </li>
    </ul>
    <p class="contacts__address">17 Harbour Rd., Eastvale,<br>NSW 2150</p>
    <p class="contacts__abn">ABN 73 215 904 386</p>

    <div class="brand">
      <span class="brand__dot"></span>
      <span class="brand__name">TBK Plumbing</span>
    </div>

    <div class="company-band">TBK Plumbing Services Pty Ltd.</div>
  </section>

</body>
</html>
```